Create the design of Sitelaunch (in photoshop or similar)

*edit* What we wanna see is a sketch of a first page, and then in the end 5 page designs, but the main page will be the big tasks other pages are just basically pop-ups or form. *edit*

We need a web design for our new startup Sitelaunch in turn will be providing web pages to smaller business. So the purpose of the page is to clearly showcase the message in a web 3.0 fashion, good design looks but function should always be the main focus.Further more we are looking for a long term relationship with a good designer / design company that can help us design the future web sites for our customers as well.

We need you to understand web, not just design. You need to be up to date with how web looks and works, and how to make it as simple and easy to use as possible for the customer and at the same time good looking.

Colors and layout are free to choose, but we really like the kind of layout that forkcomet.com has so feel free to be inspired by them.

We want all of the pages design, but the main/landing page will be the big part, the rest are small pages that will use the same design frame as the main page.

PS. We just want the design in photoshop or illustrator format, the website will then be built in word press by word press experts (let us know if you/company also possess this knowledge)

Target Market(s)

Small to medium sized business, mostly owner/entrepreneur driven companies.

Industry/Entity Type

Business

Font styles to use
Other font styles liked:
• Helvetica for the win

Requirements
Must have
• Great and simple design, a child should be able to understand the message and also enjoy reading it. Should be a funny website while still being professional, i.e. see postbadger.com for example.

```html
<!DOCTYPE html>
<html lang="en">
<head>
<meta charset="utf-8">
<title>Sitelaunch – Home</title>
<link href="https://fonts.googleapis.com/css2?family=Kreon:wght@300;400;700&display=swap" rel="stylesheet">
<style>
:root{
  --teal:#1aafa5;
  --teal-dark:#11958c;
  --purple:#8b1a8e;
  --purple-dark:#6e1370;
  --page:#eef4f4;
  --band:#e6e8e8;
  --card:#f7f8f8;
  --text:#555b5c;
  --muted:#8a9091;
  --white:#ffffff;
  --photo-warm:#b99a6e;
  --photo-cool:#8aa4ad;
}
*{margin:0;padding:0;box-sizing:border-box}
html,body{width:1043px;height:1200px;overflow:hidden}
body{position:relative;background:var(--page);font-family:"Kreon",Georgia,serif;color:var(--text)}
.abs{position:absolute}

/* header */
.topbar{left:0;top:0;width:1043px;height:20px;background:#f3f5f5;font-size:10px;color:var(--muted)}
.topbar .info{left:228px;top:4px;display:flex;gap:18px}
.topbar .info span::before{content:"";display:inline-block;width:8px;height:8px;border:1px solid var(--muted);border-radius:50%;margin-right:5px;vertical-align:-1px}
.checkout{left:744px;top:2px;font-size:12px;color:var(--purple);font-weight:700}
.navbar{left:0;top:20px;width:1043px;height:43px;background:var(--white);border-bottom:3px solid var(--purple)}
.brand{left:228px;top:7px;display:flex;align-items:center;gap:6px;font-size:22px;font-weight:700;color:var(--teal)}
.brand i{width:18px;height:18px;border-radius:50%;background:var(--purple);display:block}
.nav{right:224px;top:14px;display:flex;gap:22px;font-size:10px;color:var(--teal);letter-spacing:.3px}

/* hero */
.hero{left:0;top:63px;width:1043px;height:242px;background:linear-gradient(120deg,#d9ddd8 0%,var(--photo-warm) 40%,#5f4a32 60%,var(--photo-cool) 100%)}
.hero-title{left:224px;top:160px;font-size:21px;line-height:28px;color:var(--white)}
.hero-title span{background:rgba(90,30,90,.55);padding:1px 8px}
.arrow{top:168px;width:26px;height:32px;background:var(--purple);color:var(--white);font-size:18px;text-align:center;line-height:30px}
.dots{left:470px;top:312px;display:flex;gap:6px}
.dots i{width:31px;height:3px;background:#bcc5c5;display:block}
.dots i.on{background:var(--teal)}

/* services intro */
.services-bar{left:224px;top:323px;width:595px;height:51px;background:#e3e6e6}
.services-bar h2{position:absolute;left:14px;top:9px;font-size:17px;font-weight:300;color:#777}
.services-bar p{position:absolute;left:14px;top:31px;font-size:8px;color:var(--muted)}
.btn{display:block;text-align:center;color:var(--white);font-size:11px;border-radius:2px}
.btn-purple{background:var(--purple);box-shadow:0 3px 0 var(--purple-dark)}
.btn-teal{background:var(--teal);box-shadow:0 3px 0 var(--teal-dark)}
.services-bar .btn{position:absolute;left:475px;top:11px;width:102px;height:26px;line-height:26px;font-size:12px}

.card{top:399px;width:137px;height:159px;background:var(--card);text-align:center}
.card svg{display:block;margin:24px auto 12px}
.card h3{font-size:10px;font-weight:400;color:#666;letter-spacing:.3px}
.card p{font-size:7px;line-height:10px;color:var(--muted);padding:5px 14px 0}
.card .btn{position:absolute;left:20px;top:144px;width:101px;height:25px;line-height:25px}

/* why band */
.why-band{left:0;top:587px;width:1043px;height:202px;background:var(--band)}
.why-title{left:0;width:1043px;top:616px;text-align:center;font-size:25px;color:var(--purple)}
.why-sub{left:0;width:1043px;top:642px;text-align:center;font-size:8px;color:var(--muted)}
.screen{background:#c9cfcf;border-radius:3px;padding:15px 5px 5px}
.screen .photo{width:100%;height:100%}
.screen::before{content:"● ● ●";position:absolute;left:6px;top:2px;font-size:6px;color:var(--white);letter-spacing:1px}

/* lower section */
.lower h4{font-size:11px;font-weight:400;color:#666}
.checklist{list-style:none;font-size:8px;line-height:13px;color:var(--muted);margin-top:12px}
.checklist li::before{content:"◆";color:#d0403b;font-size:6px;margin-right:6px}
.lead{font-size:8px;line-height:12px;color:var(--muted)}
.lead a{color:var(--purple)}
.gauge{width:60px;text-align:center;font-size:8px;color:var(--purple)}
.gauge svg{display:block;margin:0 auto 4px}
.quote{background:var(--white);font-size:8px;line-height:12px;color:var(--muted);font-style:italic;padding:8px 12px}
.quote-name{font-size:10px;color:#666}

/* footer */
.footer{left:0;top:1017px;width:1043px;height:157px;background:var(--teal);color:var(--white)}
.footer .brand-foot{left:228px;top:20px;font-size:22px;font-weight:700}
.footer h5{font-size:12px;font-weight:400}
.footer ul{list-style:none;font-size:8px;line-height:12px;margin-top:12px}
.footer ul li::before{content:"›";margin-right:5px}
.foot-about{left:228px;top:50px;width:200px;font-size:8px;line-height:12px}
.foot-contact{left:228px;top:96px;font-size:9px;line-height:16px}
.foot-contact b{font-size:12px;font-weight:400;margin-left:18px}
.blog-item{display:flex;gap:10px;margin-top:12px}
.blog-item i{width:36px;height:36px;background:var(--teal-dark);display:block}
.blog-item p{font-size:8px;line-height:11px}
.blog-item small{font-size:7px;opacity:.8}
.bottombar{left:0;top:1174px;width:1043px;height:26px;background:var(--teal-dark);color:var(--white);font-size:8px}
.social{right:224px;top:7px;display:flex;gap:10px}
.social i{width:12px;height:12px;border-radius:50%;background:var(--white);display:block}
</style>
</head>
<body>

<header>
  <div class="abs topbar">
    <div class="abs info"><span>east bay</span><span>delivery ~10 mins</span><span>open 10:00 am - 2:00 pm</span></div>
    <div class="abs checkout">CHECKOUT »</div>
  </div>
  <div class="abs navbar">
    <div class="abs brand"><i></i>Sitelaunch</div>
    <nav class="abs nav"><span>HOME</span><span>ABOUT US</span><span>HOW IT WORKS</span><span>CONTACT US</span><span>FAQ</span><span>ORDER</span></nav>
  </div>
</header>

<section>
  <div class="abs hero" role="img" aria-label="Photo of chilled bottles on ice"></div>
  <h1 class="abs hero-title" style="font-weight:400"><span>Your website on subscription autopilot</span><br><span>with free unlimited support and updates.</span></h1>
  <div class="abs arrow" style="left:0">«</div>
  <div class="abs arrow" style="right:0">»</div>
  <div class="abs dots"><i></i><i class="on"></i><i></i></div>
</section>

<section>
  <div class="abs services-bar">
    <h2>Some of our top services</h2>
    <p>Simple websites for small teams, built fast and kept fresh every month for you.</p>
    <span class="btn btn-purple">VIEW MORE</span>
  </div>

  <div class="abs card" style="left:224px">
    <svg width="28" height="28" viewBox="0 0 28 28"><circle cx="14" cy="8" r="6" fill="var(--purple)"/><path d="M2 28c0-8 5-12 12-12s12 4 12 12z" fill="var(--purple)"/></svg>
    <h3>WHAT IS SITELAUNCH?</h3>
    <p>We build and run a site for your business so you can focus on your work.</p>
    <span class="btn btn-purple">read more</span>
  </div>
  <div class="abs card" style="left:378px">
    <svg width="34" height="28" viewBox="0 0 34 28"><ellipse cx="16" cy="16" rx="13" ry="10" fill="none" stroke="var(--teal)" stroke-width="2"/><circle cx="27" cy="4" r="3" fill="none" stroke="var(--teal)" stroke-width="2"/><path d="M8 25v3M23 25v3" stroke="var(--teal)" stroke-width="2"/></svg>
    <h3>WHAT DOES IT COST?</h3>
    <p>One small monthly fee covers hosting, support and updates with no surprise costs.</p>
    <span class="btn btn-teal">read more</span>
  </div>
  <div class="abs card" style="left:528px">
    <svg width="28" height="28" viewBox="0 0 28 28"><path d="M4 26l10-10M12 12l4-4 6 6-4 4z" stroke="var(--teal)" stroke-width="3" fill="var(--teal)"/><path d="M18 6l4-4 4 4-4 4" fill="var(--teal)"/></svg>
    <h3>TEST YOUR WEBSITE NOW!</h3>
    <p>Try a live demo of your new site today and see how it works for you.</p>
    <span class="btn btn-teal">read more</span>
  </div>
  <div class="abs card" style="left:681px">
    <svg width="34" height="28" viewBox="0 0 34 28"><rect x="2" y="8" width="26" height="16" rx="2" fill="var(--teal)" transform="rotate(-12 15 16)"/><circle cx="16" cy="15" r="4" fill="var(--white)"/></svg>
    <h3>IF YOU ARE UNHAPPY?</h3>
    <p>Cancel at any time with no questions asked and keep your content.</p>
    <span class="btn btn-teal">read more</span>
  </div>
</section>

<section>
  <div class="abs why-band"></div>
  <h2 class="abs why-title" style="font-weight:400">WHY NOVA VERSO?</h2>
  <p class="abs why-sub">Clear pages, quick setup and friendly people who answer when you need help.</p>
  <div class="abs screen" style="left:224px;top:717px;width:154px;height:128px"><div class="photo" role="img" aria-label="Photo of hands holding a tablet" style="background:linear-gradient(135deg,#dfe6ea,#6f8fa8)"></div></div>
  <div class="abs screen" style="left:665px;top:717px;width:154px;height:128px"><div class="photo" role="img" aria-label="Photo of a businessman beside a bar chart" style="background:linear-gradient(135deg,#9aa3a8,#cfd6dc)"></div></div>
  <div class="abs screen" style="left:378px;top:687px;width:287px;height:178px"><div class="photo" role="img" aria-label="Photo of a hand typing on a keyboard" style="background:linear-gradient(135deg,#cfe0e8,#5d7787)"></div></div>
</section>

<section class="lower">
  <div class="abs" style="left:224px;top:895px;width:140px">
    <h4>Why Choose Us ?</h4>
    <ul class="checklist">
      <li>Quick and simple setup</li><li>Friendly local support</li><li>Fresh design each year</li><li>Works on every phone</li><li>No hidden costs</li><li>Cancel any time you like</li>
    </ul>
  </div>
  <p class="abs lead" style="left:387px;top:893px;width:272px">Every page is tested on phones and tablets, loads fast and is easy to edit. See our <a>simple plans</a> and pick what fits your shop best.</p>
  <div class="abs" style="left:380px;top:945px;display:flex;gap:16px">
    <div class="gauge"><svg width="60" height="34" viewBox="0 0 60 34"><path d="M6 32a24 24 0 0 1 48 0" fill="none" stroke="var(--purple)" stroke-width="7"/><path d="M30 8a24 24 0 0 1 24 24" fill="none" stroke="var(--teal)" stroke-width="7"/><text x="30" y="31" text-anchor="middle" font-size="14" fill="#777" font-family="Kreon, serif">50</text></svg>buying your product</div>
    <div class="gauge"><svg width="60" height="34" viewBox="0 0 60 34"><path d="M6 32a24 24 0 0 1 48 0" fill="none" stroke="var(--purple)" stroke-width="7"/><path d="M46 13a24 24 0 0 1 8 19" fill="none" stroke="var(--teal)" stroke-width="7"/><text x="30" y="31" text-anchor="middle" font-size="14" fill="#777" font-family="Kreon, serif">70</text></svg>better conversion</div>
    <div class="gauge"><svg width="60" height="34" viewBox="0 0 60 34"><path d="M6 32a24 24 0 0 1 48 0" fill="none" stroke="var(--purple)" stroke-width="7"/><path d="M50 19a24 24 0 0 1 4 13" fill="none" stroke="var(--teal)" stroke-width="7"/><text x="30" y="31" text-anchor="middle" font-size="14" fill="#777" font-family="Kreon, serif">80</text></svg>potential customers</div>
    <div class="gauge"><svg width="60" height="34" viewBox="0 0 60 34"><path d="M6 32a24 24 0 0 1 48 0" fill="none" stroke="var(--purple)" stroke-width="7"/><text x="30" y="31" text-anchor="middle" font-size="14" fill="#777" font-family="Kreon, serif">100</text></svg>average amount</div>
  </div>
  <div class="abs" style="left:677px;top:895px;width:142px">
    <h4>What Client's Say ?</h4>
    <p class="quote" style="margin-top:10px">We had a site in a week and our phone has not stopped ringing. The team is quick, kind and always there.</p>
    <p class="quote-name" style="text-align:center;margin-top:8px">Jhon Doe</p>
  </div>
</section>

<footer>
  <div class="abs footer">
    <div class="abs brand-foot">Sitelaunch</div>
    <p class="abs foot-about">Small business sites built with care, kept safe and updated every month so you never have to worry.</p>
    <p class="abs foot-contact">Phone: <b>182 2570 4413</b><br>e-mail: <b>info@sitelaunch.es</b></p>
    <div class="abs" style="left:431px;top:26px"><h5>Company</h5><ul><li>About</li><li>FAQ</li><li>Contact</li><li>Terms</li><li>Privacy</li><li>Testimonials</li></ul></div>
    <div class="abs" style="left:536px;top:26px"><h5>Community</h5><ul><li>Blog</li><li>Forum</li><li>Support</li><li>Newsletter</li></ul></div>
    <div class="abs" style="left:640px;top:26px;width:180px">
      <h5><i>from the</i> BLOG</h5>
      <div class="blog-item"><i role="img" aria-label="Blog post thumbnail"></i><p>Five easy ways to get more visitors<br><small>26. May. 2013</small></p></div>
      <div class="blog-item"><i role="img" aria-label="Blog post thumbnail"></i><p>Why your shop needs a mobile page<br><small>26. May. 2013</small></p></div>
    </div>
  </div>
  <div class="abs bottombar">
    <span class="abs" style="left:228px;top:8px">2014 sitelaunch all reserved</span>
    <div class="abs social"><i></i><i></i><i></i><i></i></div>
  </div>
</footer>

</body>
</html>
```